Business card for Luxury Portable Restroom Trailer company

We are a Luxury Portable Restroom Trailer Company Called FALCRIDGE HIRES. Based in Orange County California. We provide portable restroom trailers for events, such as, Weddings, Concerts, Charity events, Sporting events, Tournaments, Corporate events, ect. We rent and Sell the Luxury restrooms. Our colors are white, grey, and Orange. As you will see in the logo we uploaded.
There are 2 people in the company so the names and titles will change for the 3 people but card will remain the same. Here is the information for each Person: Dwight Penner CFO 555 318-0476
next Person: Leon Marchetti VP 555 318-0476
Next Person: Owen Marchetti CEO 555 318-0476
Information to include on the card: Luxury Restroom Trailers Rental and Sales. Weddings, Concerts, Charity, Sporting and Corp. Events.

```html
<!DOCTYPE html>
<html lang="en">
<head>
<meta charset="UTF-8">
<title>Falcridge Hires – Business Card</title>
<link href="https://fonts.googleapis.com/css2?family=Montserrat:wght@400;500;700;800&display=swap" rel="stylesheet">
<style>
  :root {
    --stage: #1b1b1f;
    --card: #161616;
    --card-edge: #222224;
    --orange: #f26a21;
    --white: #f2f2f2;
    --muted: #a9a9ab;
    --emboss: #2a2a2b;
    --decor-light: #4a4a4c;
    --decor-dark: #1a1a1a;
  }
  * { margin: 0; padding: 0; box-sizing: border-box; }
  html, body {
    width: 1200px; height: 900px; overflow: hidden;
    background: var(--stage);
    font-family: "Montserrat", sans-serif;
  }
  .canvas { position: relative; width: 1200px; height: 900px; }
  .card {
    position: absolute;
    width: 680px; height: 389px;
    background: var(--card);
    border-radius: 22px;
    border: 1px solid var(--card-edge);
    box-shadow: 0 18px 40px rgba(0,0,0,.55);
    overflow: hidden;
  }
  .card--back { left: 60px; top: 50px; }
  .card--front { left: 460px; top: 461px; }

  /* back */
  .back-brand {
    position: absolute; left: 0; right: 0; top: 50%;
    transform: translateY(-50%);
    display: flex; align-items: center; justify-content: center; gap: 20px;
    color: var(--emboss);
    font-weight: 800; font-size: 44px; letter-spacing: 2px;
    white-space: nowrap;
  }
  .back-brand .mark-square { width: 40px; height: 40px; background: var(--emboss); flex: none; }

  /* front */
  .accent-bar {
    position: absolute; right: 44px; top: 34px;
    width: 22px; height: 44px; background: var(--orange);
  }
  .person { position: absolute; right: 78px; top: 32px; text-align: right; white-space: nowrap; }
  .person-name { color: var(--orange); font-weight: 700; font-size: 26px; }
  .person-title { color: var(--white); font-weight: 400; font-size: 13px; margin-top: 2px; }

  .decor {
    position: absolute; right: 0; top: 120px;
    width: 260px; height: 220px;
    background: linear-gradient(135deg, var(--decor-light), var(--decor-dark) 70%);
    border-radius: 40px 0 0 40px;
    opacity: .8;
  }

  .brand {
    position: absolute; left: 44px; top: 72px;
    display: flex; align-items: center; gap: 10px;
    color: var(--orange); font-weight: 800; font-size: 24px; letter-spacing: 1px;
    white-space: nowrap;
  }
  .brand .mark-square { width: 18px; height: 18px; background: var(--orange); flex: none; }

  .services {
    position: absolute; left: 44px; top: 112px; width: 340px;
  }
  .services-main { color: var(--white); font-weight: 500; font-size: 13px; }
  .services-events { color: var(--muted); font-weight: 400; font-size: 11.5px; margin-top: 4px; line-height: 1.35; }

  .address {
    position: absolute; left: 44px; top: 196px;
    color: var(--white); font-size: 15px; line-height: 1.35;
  }
  .contacts {
    position: absolute; left: 44px; top: 256px;
    list-style: none; color: var(--white); font-size: 15px;
  }
  .contacts li { display: flex; align-items: center; gap: 12px; height: 26px; white-space: nowrap; }
  .contacts svg { width: 16px; height: 16px; fill: var(--orange); flex: none; }
</style>
</head>
<body>
<main class="canvas">

  <section class="card card--back" aria-label="Card back">
    <div class="back-brand">
      <span class="mark-square"></span>
      <span>FALCRIDGE HIRES</span>
    </div>
  </section>

  <section class="card card--front" aria-label="Card front">
    <div class="accent-bar"></div>
    <div class="person">
      <p class="person-name">Owen Marchetti</p>
      <p class="person-title">CEO</p>
    </div>

    <div class="decor" role="img" aria-label="Large glossy brand symbol decoration"></div>

    <div class="brand">
      <span class="mark-square"></span>
      <span>FALCRIDGE HIRES</span>
    </div>

    <div class="services">
      <p class="services-main">Luxury Restroom Trailers Rental and Sales</p>
      <p class="services-events">Weddings, Concerts, Charity, Sporting and Corp. Events</p>
    </div>

    <p class="address">418 Harbor Crest Ave, #112<br>Lakemont, CA 92605</p>

    <ul class="contacts">
      <li>
        <svg viewBox="0 0 16 16" aria-hidden="true"><path d="M2 5c0-2 2-3 6-3s6 1 6 3v1h-3V5H5v1H2zM4 7h8l2 6H2z"/></svg>
        555 318-0476
      </li>
      <li>
        <svg viewBox="0 0 16 16" aria-hidden="true"><path d="M4 1h8v14H4zM5.5 3v9h5V3z"/></svg>
        555 318-0476
      </li>
      <li>
        <svg viewBox="0 0 16 16" aria-hidden="true"><path d="M1 3h14v10H1zM2.5 4.5 8 9l5.5-4.5z"/></svg>
        info@falcridgehires.com
      </li>
      <li>
        <svg viewBox="0 0 16 16" aria-hidden="true"><path d="M8 1a7 7 0 1 0 0 14A7 7 0 0 0 8 1zm0 1.8c.9 1 1.5 2.6 1.6 4.2H6.4C6.5 5.4 7.1 3.8 8 2.8zM6.4 9h3.2c-.1 1.6-.7 3.2-1.6 4.2-.9-1-1.5-2.6-1.6-4.2z"/></svg>
        www.falcridgehires.com
      </li>
    </ul>
  </section>

</main>
</body>
</html>
```